Business Card Re-Design/Update

We'd like to update out business cards. I've included our current "Style guide" which has the colour scheme of the organisation in it. I've also included the branding files with logos etc in them.

I've also included a copy of one of our existing cards so that you can see how ugly/dated they look. I'd like a fresh modern corporate look.

Target Market(s)

These are for our clients, potential clients, industry contacts - like all business cards

Contact Information for Business Card

Name
Position
Company Address - Level 1, 47 Fernby Street, Carlow Qld 4072
Direct Phone
mobile
Email
Website -www.korvalit.com.au
Logo

Colors

Designer to choose colors to be used in the design.

Requirements
Must have
• Main Logo
• Cards will need to be editable to be able to personalize them for each new employee.
Nice to have
• The MapOut, ShipWell, KeepSteady would be okay to have if they can be sensibly and professionally added to the look without detracting from the main imagery.
• Maybe they could go on the back of the card? will leave this to your creative discretion as to whether/where they fit.
Should not have
• Should not have decorative or script fonts

```html
<!DOCTYPE html>
<html lang="en">
<head>
<meta charset="utf-8">
<title>KorvalIT Business Card</title>
<link rel="stylesheet" href="https://fonts.googleapis.com/css2?family=Roboto:wght@400;500;700&display=swap">
<style>
  :root {
    --page: #3a332f;
    --card: #1f2022;
    --card-edge: #2a2b2e;
    --white: #f4f4f4;
    --grey: #8a8b8e;
    --red: #d8232a;
    --green: #5a9a3a;
    --blue: #2f86c4;
    --magenta: #b0287f;
    --rule: #6a6b6e;
  }
  * { box-sizing: border-box; margin: 0; padding: 0; }
  html, body { width: 1200px; height: 769px; overflow: hidden; }
  body {
    background: var(--page);
    font-family: "Roboto", Arial, sans-serif;
    display: flex;
    align-items: center;
    justify-content: center;
    gap: 48px;
  }
  .card {
    width: 540px;
    height: 330px;
    background: var(--card);
    border: 1px solid var(--card-edge);
    position: relative;
    box-shadow: 0 10px 28px rgba(0,0,0,.45);
  }
  .mark { display: inline-block; }

  /* back */
  .card-back .brand {
    position: absolute;
    left: 0; right: 0; top: 92px;
    display: flex; align-items: center; justify-content: center; gap: 14px;
  }
  .card-back .brand .mark { width: 46px; height: 46px; background: #34353a; }
  .card-back .brand-name { font-size: 56px; font-weight: 500; color: var(--grey); letter-spacing: -1px; }
  .services {
    position: absolute; left: 0; right: 0; bottom: 74px;
    display: flex; justify-content: center; gap: 34px;
  }
  .service { display: flex; align-items: center; gap: 7px; font-size: 22px; font-weight: 400; }
  .service .mark { width: 14px; height: 14px; }
  .service-map { color: var(--green); } .service-map .mark { background: var(--green); }
  .service-ship { color: var(--blue); } .service-ship .mark { background: var(--blue); }
  .service-keep { color: var(--magenta); } .service-keep .mark { background: var(--magenta); }

  /* front */
  .card-front .brand {
    position: absolute; left: 34px; top: 138px;
    display: flex; align-items: center; gap: 12px;
  }
  .card-front .brand .mark { width: 34px; height: 34px; background: var(--red); }
  .card-front .brand-name { font-size: 38px; font-weight: 500; color: var(--white); letter-spacing: -.5px; }
  .divider {
    position: absolute; left: 262px; top: 40px; bottom: 40px;
    width: 1px; background: linear-gradient(var(--card), var(--rule) 30%, var(--rule) 70%, var(--card));
  }
  .contact { position: absolute; left: 286px; top: 52px; color: var(--white); font-size: 14px; line-height: 1.45; }
  .contact .name { color: var(--red); font-size: 19px; font-weight: 700; text-transform: uppercase; letter-spacing: .3px; }
  .contact .role { font-weight: 500; margin-bottom: 6px; }
  .contact .address { margin-bottom: 6px; }
  .contact ul { list-style: none; }
  .contact li { display: flex; align-items: center; gap: 8px; }
  .contact svg { width: 12px; height: 12px; fill: var(--red); flex: none; }
</style>
</head>
<body>
  <section class="card card-back" aria-label="Card back">
    <div class="brand"><span class="mark"></span><span class="brand-name">korvalIT</span></div>
    <div class="services">
      <span class="service service-map"><span class="mark"></span>MapOut</span>
      <span class="service service-ship"><span class="mark"></span>ShipWell</span>
      <span class="service service-keep"><span class="mark"></span>KeepSteady</span>
    </div>
  </section>

  <section class="card card-front" aria-label="Card front">
    <div class="brand"><span class="mark"></span><span class="brand-name">korvalIT</span></div>
    <div class="divider"></div>
    <div class="contact">
      <p class="name">Mara Ellison</p>
      <p class="role">Business Development Manager</p>
      <p class="address">Level 1, 47 Fernby Street<br>Carlow Qld 4072</p>
      <ul>
        <li><svg viewBox="0 0 12 12"><path d="M2 1h3l1 3-2 1a7 7 0 0 0 3 3l1-2 3 1v3c-6 0-9-3-9-9z"/></svg>+61 (0)7 3400 1200</li>
        <li><svg viewBox="0 0 12 12"><path d="M2 1h3l1 3-2 1a7 7 0 0 0 3 3l1-2 3 1v3c-6 0-9-3-9-9z"/></svg>+61 (0)7 3400 1215</li>
        <li><svg viewBox="0 0 12 12"><path d="M3 0h6v12H3zM4 1v8h4V1z"/></svg>+61 (0)412 555 018</li>
        <li><svg viewBox="0 0 12 12"><path d="M3 0h6v3H3zM1 4h10v6H1zM3 9h6v3H3z"/></svg>+61 (0)7 3400 1299</li>
        <li><svg viewBox="0 0 12 12"><path d="M0 2h12v8H0zM1 3l5 4 5-4z"/></svg>mellison@korvalit.com.au</li>
        <li><svg viewBox="0 0 12 12"><circle cx="6" cy="6" r="6"/></svg>www.korvalit.com.au</li>
      </ul>
    </div>
  </section>
</body>
</html>
```